Business Cards for new orthopaedic surgery practice

My husband and I are starting our own orthopaedic surgery practice. We are looking for a business card that is uniform, but one will have my name/title and the other will have his. You can just create one design with my name on it for now. But when I choose your design as the winning design I will ask that you add another copy with his name/title.

We are looking for classy, simple, elite all in one. We like dark blues/a little gold/yellow. Something that goes with our logo. We want our logo incorporated. Here is all the info you need:
Business name: RV Bone & Vitality Center
Location: 38517 North Willowmere Ave
Coral Springs, FL 33071
Phone: 954-218-4063
Fax: 954-582-7341
Email: info@myrvbonecare.example

Names: Lydia Vance, M.D.
Board Certified Hand and Upper Extremity Surgeon

Ebo Dansu, M.D.
Board Certified Hip & Knee Replacement/General Orthopaedic Surgeon

Can decide what you want to put on the back. Maybe a slogan:
Rooted in Care. Focused on You

I am just going to upload our logo. The only thing is if we select you as the winning design, the location, and phone numbers may change. We will need your help to update that once fully solidified.

Industry/Entity Type

Medical

Contact Information for Business Card

Colors
0054AA
0677BA
7BADD7
CADEEF
E8F1F8
0094D4
00A9DD
6FCCEA
C7EBF8
E9F6FB

Requirements
Must have
• class, appeal,
Should not have
• We want to air on the side of masculine if we are looking at masculine vs. feminine feel. But we still want it classy, sophisticated, and something we will love

```html
<!DOCTYPE html>
<html lang="en">
<head>
<meta charset="utf-8">
<title>RV Bone &amp; Vitality Center – Business Card</title>
<link rel="stylesheet" href="https://fonts.googleapis.com/css2?family=Marcellus&family=Roboto:wght@400&display=swap">
<style>
  :root {
    --navy: #233f85;
    --sky: #1ab4dd;
    --back-blue: #2a3a8e;
    --ink: #555a60;
    --rule: #5c6c9c;
    --page: #f2f2f2;
    --paper: #ffffff;
  }
  * { margin: 0; padding: 0; box-sizing: border-box; }
  html, body { width: 1188px; height: 1200px; overflow: hidden; background: var(--page); }
  .card {
    position: absolute;
    left: 245px;
    width: 696px;
    height: 386px;
    overflow: hidden;
  }
  .card-front { top: 159px; background: var(--paper); }
  .card-back { top: 627px; background: var(--sky); }

  .top-band { position: absolute; left: 0; top: 0; width: 696px; height: 17px; }

  .practice-name {
    position: absolute;
    left: 380px; top: 62px;
    width: 268px;
    text-align: center;
    font-family: "Marcellus", serif;
    font-size: 24px;
    line-height: 30px;
    letter-spacing: 0.5px;
    text-transform: uppercase;
    color: var(--navy);
  }

  .doctor-name {
    position: absolute;
    left: 51px; top: 177px;
    font-family: "Marcellus", serif;
    font-size: 22px;
    letter-spacing: 0.3px;
    color: var(--navy);
  }
  .doctor-title {
    position: absolute;
    left: 51px; top: 201px;
    font-family: "Roboto", sans-serif;
    font-size: 18px;
    color: var(--sky);
  }
  .divider {
    position: absolute;
    left: 51px; top: 238px;
    width: 592px; height: 1px;
    background: var(--rule);
  }

  .contact-list {
    position: absolute;
    left: 51px; top: 251px;
    list-style: none;
    font-family: "Roboto", sans-serif;
    font-size: 18px;
    color: var(--ink);
  }
  .contact-list li { display: flex; align-items: center; height: 24.5px; }
  .contact-list svg { width: 18px; height: 18px; margin-right: 6px; fill: var(--navy); }

  .address {
    position: absolute;
    left: 463px; top: 272px;
    display: flex;
    font-family: "Roboto", sans-serif;
    font-size: 18px;
    line-height: 25.5px;
    color: var(--ink);
  }
  .address svg { width: 16px; height: 22px; margin-top: 2px; margin-right: 10px; fill: var(--navy); }

  .back-field {
    position: absolute;
    left: 3px; top: 0;
    width: 693px; height: 383px;
    background: linear-gradient(135deg, #36479a 0%, var(--back-blue) 55%, #25358a 100%);
  }
  .back-name {
    position: absolute;
    left: 455px; top: 222px;
    width: 200px;
    text-align: center;
    font-family: "Marcellus", serif;
    font-size: 20px;
    line-height: 25px;
    text-transform: uppercase;
    color: var(--paper);
  }
</style>
</head>
<body>

<section class="card card-front">
  <svg class="top-band" viewBox="0 0 696 17" aria-hidden="true">
    <rect width="696" height="17" fill="var(--sky)"/>
    <polygon points="0,0 521,0 507,17 0,17" fill="var(--navy)"/>
    <polygon points="521,0 525,0 511,17 507,17" fill="#ffffff"/>
  </svg>

  <div class="practice-name">RV Bone &amp; Vitality<br>Center</div>

  <h1 class="doctor-name">LYDIA VANCE, M.D.</h1>
  <p class="doctor-title">Board Certified Hand and Upper Extremity Surgeon</p>
  <div class="divider"></div>

  <ul class="contact-list">
    <li>
      <svg viewBox="0 0 24 24" aria-hidden="true"><path d="M3 9c0-3 4-5 9-5s9 2 9 5v2h-5V9c-1-.5-2.5-.8-4-.8S9 8.5 8 9v2H3zM6 12h12l2 8H4z"/></svg>
      954-641-2290
    </li>
    <li>
      <svg viewBox="0 0 24 24" aria-hidden="true"><path d="M7 3h10v5H7zM4 9h16v8h-3v4H7v-4H4zM9 14v5h6v-5z"/></svg>
      800-417-3365
    </li>
    <li>
      <svg viewBox="0 0 24 24" aria-hidden="true"><path d="M2 6h20v12H2zM4 8v.4l8 5.6 8-5.6V8l-8 5.3z"/></svg>
      info@myrvbonecare.example
    </li>
    <li>
      <svg viewBox="0 0 24 24" aria-hidden="true"><circle cx="12" cy="12" r="10"/><path d="M8 6c2 1 3 3 1 5s0 4 2 5l-1 4M15 5c-1 2 1 3 3 3M16 14c1 1 2 2 2 4" stroke="#fff" stroke-width="1.6" fill="none"/></svg>
      www.lvancehand.example
    </li>
  </ul>

  <div class="address">
    <svg viewBox="0 0 16 22" aria-hidden="true"><path d="M8 0a8 8 0 0 1 8 8c0 6-8 14-8 14S0 14 0 8a8 8 0 0 1 8-8zm0 4.5a3.5 3.5 0 1 0 0 7 3.5 3.5 0 0 0 0-7z"/></svg>
    <p>2950 Larkfield Ct,<br>STE 8 Brookhaven,<br>FL 33099</p>
  </div>
</section>

<section class="card card-back">
  <div class="back-field" role="img" aria-label="Embossed repeating practice monogram pattern in tonal blue and silver"></div>
  <div class="back-name">RV Bone &amp;<br>Vitality Center</div>
</section>

</body>
</html>
```